Animation College website

Name of College: Brightloom Academy of 3D Animation and VFX

We need a redesigned modern website for Brightloom. The web-design should communicate a VFX and animation school and education. We will also need full access to the website once completed. We will also need access to the website to be able to make changes to the content and site ideally the website would be built on Wordpress.

To learn more about what the College please visit: http://brightloom-academy.example/
The video on the homepage demonstrates why Brightloom is a unique college offering 3D animation and VFX. The direct link to the video can be watched here: https://videohost.example/482915036

Client Profile Summary: Brightloom is an improved concept in job skills training for the 3D animation and visual effects industries. Our high graduate job placement numbers are based on the assertion that job skills must include more than simply learning to use software tools. Where nearly every digital media program teaches tools, job skills training should be about learning how to do a job in addition to learning how to use software tools. Brightloom is taught in an apprenticeship style with very experienced faculty mentoring and teaching students to learn how to master their craft (VFX and animation) so they can seamlessly step into industry and excel.

Target Market(s)

High school students, students interested in learning about animation and 3D.

Industry/Entity Type

College

Coding

Coded - Design and coding required

Number of Pages Required

5+ page

Font styles to use
Sans Serif

Colors

Designer to choose colors to be used in the design.

Requirements
Must have
• Please include the video on the current Brightloom-academy.example website. https://videohost.example/482915036
• Use the same content on the current brightloom-academy.example website.
• Include a page to showcase student work.
• Website must also be mobile responsive.
Should not have
• The attached PDF of the landing page is just an example of something we like. You do not have to replicate this. The PDF landing page is showing the colour blue you should incorporate.

```html
<!DOCTYPE html>
<html lang="en">
<head>
<meta charset="utf-8">
<title>Brightloom Academy of 3D Animation and VFX</title>
<link href="https://fonts.googleapis.com/css2?family=Raleway:ital,wght@0,400;0,500;0,600;0,700;1,400;1,500;1,700&display=swap" rel="stylesheet">
<style>
:root{
  --blue:#1474c4;
  --blue-dark:#0f5fa3;
  --orange:#f39a16;
  --ink:#2b2b2b;
  --body:#555;
  --muted:#8a8a8a;
  --dark:#141414;
  --footer:#2e2e2e;
  --line:#d6d6d6;
  --white:#fff;
}
*{box-sizing:border-box;margin:0;padding:0}
html,body{width:1200px;height:3109px;overflow:hidden}
body{font-family:"Raleway",Arial,sans-serif;color:var(--body);background:var(--white);position:relative}
.section{position:absolute;left:0;width:1200px}

/* hero */
.hero{top:0;height:601px;background:linear-gradient(135deg,#2a2c30 0%,#3d4148 35%,#1c1e22 70%,#0d0e10 100%)}
.hero-photo{position:absolute;inset:0;background:radial-gradient(ellipse at 55% 30%,rgba(150,165,185,.45),rgba(0,0,0,0) 55%),linear-gradient(180deg,rgba(0,0,0,.25),rgba(0,0,0,.55))}
.brand{position:absolute;left:74px;top:34px;display:flex;align-items:center;gap:12px;color:var(--white)}
.brand-mark{width:46px;height:46px;background:var(--blue);border-radius:4px}
.brand-name{font-weight:700;font-size:26px;line-height:1}
.brand-tag{font-size:12px;font-weight:500;margin-top:4px}
.topbar{position:absolute;right:74px;top:42px;display:flex;align-items:center;gap:36px;color:var(--white);font-size:16px;font-weight:600}
.phone{display:flex;align-items:center;gap:12px}
.hero-caption{position:absolute;left:77px;top:413px}
.hero-title{display:inline-block;background:rgba(0,0,0,.85);color:var(--white);font-style:italic;font-weight:700;font-size:21px;padding:6px 12px}
.hero-sub{display:block;margin-top:9px;width:520px;background:var(--orange);color:var(--white);font-size:16px;font-weight:500;padding:6px 12px}

/* enquiry form */
.enquiry{position:absolute;left:794px;top:145px;width:332px;height:570px;background:var(--white);box-shadow:0 4px 18px rgba(0,0,0,.25);z-index:5}
.enquiry-head{background:var(--blue);color:var(--white);text-align:center;font-weight:700;font-size:20px;height:52px;line-height:52px;letter-spacing:.5px}
.enquiry-intro{text-align:center;font-style:italic;font-size:13.5px;color:#444;line-height:20px;padding:14px 18px 10px}
.field{margin:0 18px 10px;border:1px solid var(--line);height:36px;font-size:12px;color:var(--muted);padding:0 12px;line-height:34px}
.field.comments{height:126px}
.submit{margin:14px 18px 0;height:54px;background:#2f2f2f;color:var(--white);text-align:center;line-height:54px;font-weight:700;font-size:17px;letter-spacing:.5px}

/* accreditation band */
.badges{top:601px;height:160px;background:var(--blue)}
.badge-row{position:absolute;left:74px;top:26px;display:flex;gap:44px;align-items:center;height:110px}
.badge{background:rgba(255,255,255,.9)}
.badge.sq{width:72px;height:110px;border-radius:4px}
.badge.ci{width:100px;height:100px;border-radius:50%}
.badge.rect{width:124px;height:100px;border-radius:4px;background:rgba(255,255,255,.2)}

/* copy blocks */
.copy{padding:0 78px 0 75px}
.copy h2{font-size:29px;font-weight:500;color:var(--ink);line-height:1.2}
.copy .lede{font-style:italic;font-size:18px;color:var(--blue);margin:20px 0 8px}
.copy p{font-size:13.5px;line-height:26px}
.copy .label{color:var(--ink);font-weight:600;margin-top:12px}
.steps{list-style:none;margin-top:10px}
.steps li{font-size:13.5px;line-height:34px;display:flex;gap:22px}
.steps li b{color:var(--blue);width:12px}
.ticks{list-style:none;margin-top:10px}
.ticks li{font-size:13.5px;line-height:34px;display:flex;align-items:center;gap:16px}

.intro{top:761px;height:275px;padding-top:40px}

/* video */
.video{top:1036px;height:434px;background:radial-gradient(ellipse at 70% 40%,#3a2a1a,#1a1612 55%,#0b0b0b)}
.player{position:absolute;left:255px;top:27px;width:692px;height:382px;background:linear-gradient(120deg,#3b3a38,#6b5a4c 40%,#2a2d33 75%,#1b1b1b);border:2px solid #555}
.play{position:absolute;left:312px;top:166px;width:60px;height:42px;border-radius:6px;background:rgba(40,40,40,.75)}
.controls{position:absolute;left:0;right:0;bottom:0;height:28px;background:rgba(0,0,0,.75)}
.progress{position:absolute;left:40px;right:80px;top:12px;height:4px;background:#555}
.side-icons{position:absolute;right:10px;top:10px;display:flex;flex-direction:column;gap:14px}
.side-icons span{width:12px;height:12px;border-radius:50%;background:#ddd}

.experts{top:1470px;height:363px;padding-top:38px}

/* testimonial */
.quote{top:1833px;height:431px;background:linear-gradient(180deg,#1b2230,#2c3445 50%,#151a24)}
.quote-card{position:absolute;left:257px;top:82px;width:686px;height:266px;background:rgba(20,116,196,.85);border:3px solid rgba(255,255,255,.55);text-align:center;color:var(--white)}
.avatar{position:absolute;left:293px;top:-38px;width:100px;height:100px;border-radius:50%;border:4px solid var(--white);background:linear-gradient(135deg,#7a8c6a,#3e5a3a)}
.qmark{position:absolute;font-size:80px;font-family:Georgia,serif;color:rgba(255,255,255,.35);line-height:1}
.qmark.open{left:18px;top:10px}
.qmark.close{right:20px;bottom:-26px}
.quote-text{margin:78px 60px 0;font-style:italic;font-size:16px;line-height:27px}
.quote-name{font-weight:700;font-size:16px;margin-top:26px}
.quote-role{font-style:italic;font-size:13px;margin-top:8px}

.advantage{top:2264px;height:520px;padding-top:42px}

/* call to action */
.cta{top:2784px;height:174px;background:var(--blue);color:var(--white);text-align:center}
.cta h3{font-weight:400;font-size:29px;margin-top:54px}
.cta p{font-size:17px;letter-spacing:.5px;margin-top:12px}

/* footer */
.footer{top:2958px;height:151px;background:var(--footer);text-align:center}
.footer p{font-size:12px;color:#999;margin-top:50px}
.social{display:flex;justify-content:center;gap:22px;margin-top:18px}
.social span{width:20px;height:20px;border-radius:50%;background:#888}
</style>
</head>
<body>

<header class="section hero">
  <div class="hero-photo" role="img" aria-label="Student working at animation software on dual monitors in a studio"></div>
  <div class="brand">
    <div class="brand-mark"></div>
    <div>
      <div class="brand-name">Brightloom</div>
      <div class="brand-tag">Brightloom Academy of 3D Animation and VFX</div>
    </div>
  </div>
  <div class="topbar">
    <span class="phone">
      <svg width="14" height="14" viewBox="0 0 24 24"><path fill="#fff" d="M6.6 10.8a15.1 15.1 0 0 0 6.6 6.6l2.2-2.2c.3-.3.7-.4 1-.2 1.1.4 2.3.6 3.6.6.6 0 1 .4 1 1V20c0 .6-.4 1-1 1A17 17 0 0 1 3 4c0-.6.4-1 1-1h3.5c.6 0 1 .4 1 1 0 1.3.2 2.5.6 3.6.1.3 0 .7-.2 1z"/></svg>
      555-014-2290
    </span>
    <svg width="28" height="22" viewBox="0 0 28 22"><rect width="28" height="4" fill="#fff"/><rect y="9" width="28" height="4" fill="#fff"/><rect y="18" width="28" height="4" fill="#fff"/></svg>
  </div>
  <div class="hero-caption">
    <span class="hero-title">3D Animation &amp; VFX One-Year Intensive Training Program</span>
    <span class="hero-sub">Train alongside passionate and experienced industry masters</span>
  </div>
</header>

<aside class="enquiry">
  <div class="enquiry-head">WANT TO KNOW MORE?</div>
  <p class="enquiry-intro">Complete this form to receive more information about program details &amp; more!</p>
  <div class="field">First Name*</div>
  <div class="field">Last Name*</div>
  <div class="field">Phone*</div>
  <div class="field">Email Address*</div>
  <div class="field">Country of Residence*</div>
  <div class="field comments">Comments</div>
  <div class="submit">SEND ME FREE INFO</div>
</aside>

<section class="section badges">
  <div class="badge-row">
    <div class="badge sq"></div>
    <div class="badge ci"></div>
    <div class="badge ci"></div>
    <div class="badge rect"></div>
    <div class="badge rect"></div>
  </div>
</section>

<section class="section intro copy">
  <h2>One-Year Intensive Training Program</h2>
  <p class="lede">An exciting, comprehensive program 100% graduate employment rate</p>
  <p>Aliquam molestie, mi et imperdiet euismod, dui purus auctor tellus, et interdum lacus lectus et ante. Sed accumsan sollicitudin sapien, sit amet adipiscing turpis gravida ac. In congue, neque ac lobortis volutpat, libero mauris varius mi, vitae suscipit ipsum ligula vitae risus. Duis aliquam nibh a dui iaculis viverra id a velit. Vivamus egestas risus in magna varius commodo. Sed semper viverra egestas. Etiam pretium porttitor lectus, vel ornare neque porta volutpat.</p>
</section>

<section class="section video">
  <div class="player" role="img" aria-label="Video: a Brightloom graduate talks about the program">
    <div class="side-icons"><span></span><span></span><span></span><span></span></div>
    <div class="play"><svg width="60" height="42" viewBox="0 0 60 42"><path d="M24 12v18l15-9z" fill="#fff"/></svg></div>
    <div class="controls">
      <svg width="28" height="28" viewBox="0 0 28 28"><path d="M10 8v12l10-6z" fill="#fff"/></svg>
      <div class="progress"></div>
    </div>
  </div>
</section>

<section class="section experts copy">
  <h2>Learn Animation &amp; Visual Effects Production from the Experts</h2>
  <p class="lede">The world's first and sole simulated production traning program</p>
  <p>Aliquam molestie, mi et imperdiet euismod, dui purus auctor tellus, et interdum lacus lectus et ante. Sed accumsan sollicitudin sapien, sit amet adipiscing turpis gravida ac. In congue, neque ac lobortis volutpat, libero mauris varius mi, vitae suscipit ipsum ligula vitae risus.</p>
  <p class="label">Duis aliquam nibh a dui iaculis viverra id a velit egestas risus commodo.</p>
  <ol class="steps">
    <li><b>1.</b>Sed semper viverra egestaspretium porttitor lectus, vel ornare neque porta volutpat eget turpis vehicula tempus ac sed massa.</li>
    <li><b>2.</b>Vestibulum ante ipsum primis in faucibus orci luctus et ultrices posuere cubilia.</li>
    <li><b>3.</b>Vestibulum vel metus sit amet turpis bibendum tincidunt vel .</li>
  </ol>
</section>

<section class="section quote">
  <div class="quote-card">
    <div class="avatar" role="img" aria-label="Portrait of Daniel Marsh"></div>
    <span class="qmark open">&ldquo;</span>
    <p class="quote-text">"They give them the training for a real-world studio environment so when we hire graduates from Brightloom they can really fit right into our pipeline. They seem to get what it's like to work at a studio and produce really nice quality work."</p>
    <p class="quote-name">Daniel Marsh</p>
    <p class="quote-role">CG Supervisor, Northgate Pictures</p>
    <span class="qmark close">&rdquo;</span>
  </div>
</section>

<section class="section advantage copy">
  <h2>The Brightloom Advantage</h2>
  <p class="lede">Aprogram designed by industry, for industry</p>
  <p>Aliquam molestie, mi et imperdiet euismod, dui purus auctor tellus, et interdum lacus lectus et ante. Sed accumsan sollicitudin sapien, sit amet adipiscing turpis gravida ac. In congue, neque ac lobortis volutpat, libero mauris varius mi, vitae suscipit ipsum ligula vitae risus.</p>
  <p class="label">Duis aliquam nibh a dui iaculis viverra id a velit egestas risus commodo.</p>
  <ul class="ticks">
    <li><svg width="16" height="16" viewBox="0 0 16 16"><circle cx="8" cy="8" r="8" fill="#1474c4"/><path d="M4.5 8.2l2.3 2.3 4.7-4.7" stroke="#fff" stroke-width="2" fill="none"/></svg>Sed semper viverra egestaspretium porttitor lectus, vel ornare.</li>
    <li><svg width="16" height="16" viewBox="0 0 16 16"><circle cx="8" cy="8" r="8" fill="#1474c4"/><path d="M4.5 8.2l2.3 2.3 4.7-4.7" stroke="#fff" stroke-width="2" fill="none"/></svg>Volutpat eget turpis vehicula tempus ac sed massa.</li>
    <li><svg width="16" height="16" viewBox="0 0 16 16"><circle cx="8" cy="8" r="8" fill="#1474c4"/><path d="M4.5 8.2l2.3 2.3 4.7-4.7" stroke="#fff" stroke-width="2" fill="none"/></svg>Vestibulum ante ipsum primis in faucibus.</li>
    <li><svg width="16" height="16" viewBox="0 0 16 16"><circle cx="8" cy="8" r="8" fill="#1474c4"/><path d="M4.5 8.2l2.3 2.3 4.7-4.7" stroke="#fff" stroke-width="2" fill="none"/></svg>Orci luctus et ultrices posuere cubilia.</li>
    <li><svg width="16" height="16" viewBox="0 0 16 16"><circle cx="8" cy="8" r="8" fill="#1474c4"/><path d="M4.5 8.2l2.3 2.3 4.7-4.7" stroke="#fff" stroke-width="2" fill="none"/></svg>Vestibulum vel metus sit amet.</li>
    <li><svg width="16" height="16" viewBox="0 0 16 16"><circle cx="8" cy="8" r="8" fill="#1474c4"/><path d="M4.5 8.2l2.3 2.3 4.7-4.7" stroke="#fff" stroke-width="2" fill="none"/></svg>Turpis bibendum tincidunt.</li>
    <li><svg width="16" height="16" viewBox="0 0 16 16"><circle cx="8" cy="8" r="8" fill="#1474c4"/><path d="M4.5 8.2l2.3 2.3 4.7-4.7" stroke="#fff" stroke-width="2" fill="none"/></svg>And More..!</li>
  </ul>
</section>

<section class="section cta">
  <h3>Want To Learn More?</h3>
  <p>FILL OUT THE FORM ABOVE TO RECEIVE INFORMATION ABOUT THE PROGRAM.</p>
</section>

<footer class="section footer">
  <p>&copy; Copyright 2017 Brightloom Academy of 3D Animation and VFX. All Rights Reserved</p>
  <div class="social"><span></span><span></span><span></span><span></span><span></span><span></span></div>
</footer>

</body>
</html>
```